Vantro cards

I am in the auto motive, transportation business I would like a business card that is Something cool, modern edgy, having to do with car culture. I offer towing service for high and exotic cars. I also provide towing for collisions and car accidents. I offer open and enclosed transport nationwide.

Target Market(s)

Car culture people high end auto collectors

Industry/Entity Type

Towing car carrier

Contact Information for Business Card

My company colors black yellow and silver

Font styles to use
Serif

```html
<!DOCTYPE html>
<html lang="en">
<head>
<meta charset="utf-8">
<title>Vantro Business Cards</title>
<link rel="stylesheet" href="https://fonts.googleapis.com/css2?family=Poppins:wght@400;500;700&display=swap">
<style>
  :root {
    --stage: #3a3a3c;
    --ink: #0a0a0a;
    --paper: #ffffff;
    --gold: #f7d84f;
    --silver: #e6e6e6;
  }
  * { margin: 0; padding: 0; box-sizing: border-box; }
  html, body { width: 1200px; height: 1015px; overflow: hidden; }
  body {
    background: var(--stage);
    font-family: "Poppins", sans-serif;
    position: relative;
  }
  .card {
    position: absolute;
    left: 250px;
    width: 700px;
    height: 400px;
    overflow: hidden;
    box-shadow: 0 14px 30px rgba(0,0,0,.45);
  }
  .card--front { top: 70px; background: var(--ink); }
  .card--back { top: 545px; background: var(--paper); color: var(--ink); }

  .brand {
    position: absolute;
    left: 0; right: 0; top: 130px;
    display: flex; align-items: center; justify-content: center; gap: 18px;
  }
  .brand__dot {
    width: 46px; height: 46px; border-radius: 50%;
    background: var(--gold);
  }
  .brand__name {
    font-weight: 700; font-size: 64px; letter-spacing: 4px;
    color: var(--silver); text-transform: uppercase; line-height: 1;
  }
  .front-web {
    position: absolute; left: 0; right: 0; bottom: 48px;
    text-align: center; color: var(--gold);
    font-size: 20px; letter-spacing: 2px;
  }

  .side-band {
    position: absolute; left: 0; top: 150px;
    width: 70px; height: 80px; background: var(--ink);
  }
  .side-flag {
    position: absolute; left: 58px; top: 150px;
    width: 26px; height: 80px; background: var(--gold);
    transform: skewX(-10deg);
  }
  .person { position: absolute; left: 120px; top: 150px; }
  .person__name { font-weight: 700; font-size: 28px; line-height: 1.1; text-transform: uppercase; white-space: nowrap; }
  .person__role { font-size: 15px; letter-spacing: 1px; text-transform: uppercase; white-space: nowrap; }
  .address {
    position: absolute; left: 150px; top: 240px;
    font-size: 19px; line-height: 1.3; white-space: nowrap;
  }
  .contacts {
    position: absolute; left: 400px; top: 40px;
    list-style: none; font-size: 19px; line-height: 1.35;
  }
  .contacts li { display: flex; align-items: center; gap: 8px; white-space: nowrap; }
  .contacts svg { width: 16px; height: 16px; flex: none; }
  .truck-art {
    position: absolute; right: 0; bottom: 0;
    width: 310px; height: 240px;
    background: linear-gradient(150deg, #111 0%, #111 55%, var(--gold) 56%, #111 75%);
    clip-path: polygon(10% 35%, 60% 8%, 100% 0, 100% 40%, 55% 80%, 25% 100%, 0 85%);
  }
</style>
</head>
<body>
  <section class="card card--front">
    <div class="brand">
      <span class="brand__dot"></span>
      <span class="brand__name">Vantro</span>
    </div>
    <p class="front-web">www.vantrohaul.com</p>
  </section>

  <section class="card card--back">
    <div class="side-band"></div>
    <div class="side-flag"></div>
    <div class="person">
      <p class="person__name">Marcus Hale</p>
      <p class="person__role">Managing Director</p>
    </div>
    <p class="address">87, Harbor Road Line<br>30418, Eastland</p>
    <ul class="contacts">
      <li>
        <svg viewBox="0 0 16 16"><path d="M4 1l3 3-2 2c1 2 3 4 5 5l2-2 3 3-2 3C7 15 1 9 1 3z" fill="currentColor"/></svg>
        044-555 201 347
      </li>
      <li>
        <svg viewBox="0 0 16 16"><rect x="1" y="3" width="14" height="10" fill="currentColor"/><path d="M1 3l7 6 7-6" stroke="#fff" stroke-width="1.4" fill="none"/></svg>
        info@vantrohaul.com
      </li>
      <li>
        <svg viewBox="0 0 16 16"><circle cx="8" cy="8" r="7" fill="currentColor"/><path d="M1 8h14M8 1v14M3 4h10M3 12h10" stroke="#fff" stroke-width="1"/><ellipse cx="8" cy="8" rx="3" ry="7" stroke="#fff" fill="none"/></svg>
        www.vantrohaul.com
      </li>
    </ul>
    <div class="truck-art" role="img" aria-label="Black and yellow illustration of a flatbed tow truck"></div>
  </section>
</body>
</html>
```